Quiet Harbor Podcast W/ Dr. Lena Marsh

Podcast Cover Art. I am in search of a re-design for my existing podcast. We have over 100 episodes, but I want to change the name to Quiet Harbor Podcast With Dr. Lena Marsh. I'm open to any ideas, and have attached source file image to use. ( note: NO brain images please).

```html
<!DOCTYPE html>
<html lang="en">
<head>
<meta charset="utf-8">
<title>Quiet Harbor Podcast With Dr. Lena Marsh</title>
<link rel="stylesheet" href="https://fonts.googleapis.com/css2?family=Poppins:wght@500;600;700&family=Alex+Brush&display=swap">
<style>
  :root {
    --orange: #f7964d;
    --charcoal: #2b2b2b;
    --charcoal-deep: #222426;
    --white: #ffffff;
    --placeholder-top: #3a3432;
    --placeholder-bottom: #8a4a36;
  }
  html, body {
    margin: 0;
    padding: 0;
    width: 1200px;
    height: 1200px;
    overflow: hidden;
    background: var(--white);
  }
  .cover {
    display: block;
    width: 1200px;
    height: 1200px;
  }
  .show-title {
    font-family: "Poppins", sans-serif;
    font-weight: 600;
    text-anchor: middle;
  }
  .show-title--top { fill: var(--orange); font-size: 250px; }
  .show-title--bottom { fill: var(--white); font-size: 170px; }
  .host-with {
    font-family: "Alex Brush", cursive;
    fill: var(--orange);
    font-size: 78px;
    text-anchor: middle;
  }
  .host-name {
    font-family: "Poppins", sans-serif;
    font-weight: 500;
    fill: var(--white);
    font-size: 86px;
    text-anchor: middle;
  }
  .format-label {
    font-family: "Poppins", sans-serif;
    font-weight: 500;
    fill: var(--white);
    font-size: 33px;
    letter-spacing: 13px;
    text-anchor: middle;
  }
</style>
</head>
<body>
<svg class="cover" viewBox="0 0 1200 1200" xmlns="http://www.w3.org/2000/svg">
  <defs>
    <linearGradient id="portrait-placeholder" x1="0" y1="0" x2="0" y2="1">
      <stop offset="0" stop-color="var(--placeholder-top)"/>
      <stop offset="1" stop-color="var(--placeholder-bottom)"/>
    </linearGradient>
  </defs>

  <!-- background -->
  <rect class="base" x="0" y="0" width="1200" height="1200" fill="var(--charcoal)"/>

  <!-- top band: side columns and portrait panel -->
  <rect class="column column--left" x="0" y="0" width="216" height="560" fill="var(--orange)"/>
  <rect class="portrait-panel" x="216" y="0" width="807" height="560" fill="var(--charcoal-deep)"/>
  <rect class="column column--right" x="1023" y="0" width="177" height="560" fill="var(--orange)"/>

  <rect class="host-portrait" x="320" y="70" width="625" height="490"
        fill="url(#portrait-placeholder)" role="img"
        aria-label="Illustrated portrait of the host"/>

  <!-- second row accent blocks -->
  <rect class="accent-block accent-block--left" x="0" y="750" width="216" height="154" fill="var(--orange)"/>
  <rect class="accent-block accent-block--right" x="1023" y="750" width="177" height="154" fill="var(--orange)"/>

  <!-- title -->
  <text class="show-title show-title--top" x="600" y="743">QUIET</text>
  <text class="show-title show-title--bottom" x="615" y="904">HARBOR</text>

  <!-- host -->
  <text class="host-with" x="644" y="960">with</text>
  <text class="host-name" x="619" y="1055">DR. LENA MARSH</text>
  <text class="format-label" x="626" y="1121">PODCAST</text>
</svg>
</body>
</html>
```